Destination PDF Template (Editable)

Objective: Create a visually stunning and compelling PDF brochure that showcases The Vorelka Crest Lodge as the ultimate luxury hunting destination in Kyrgyzstan, specializing in Marco Polo and Ibex hunts. The PDF should evoke a sense of exclusivity, adventure, and the breathtaking beauty of the Tian Shan mountains, ultimately driving bookings.
Target Audience: High-net-worth individuals, discerning hunters seeking exceptional experiences, adventure travelers, and those interested in unique and luxurious wilderness experiences.
Overall Tone & Style: Sophisticated, elegant, and aspirational. Think high-end travel magazines combined with a touch of rugged adventure. Avoid anything that feels generic or overly commercial. The design should reflect the unparalleled nature of the lodge and the hunts offered. (I'm attaching a reference PDF that i like), as well as another instructions file. Drive link for photos: https://files.pondery-share.net/box/folders/7KqLm2xVbR4tWz9hN3cJpE6yF0aDs8uG?mode=open
Another Link: https://files.pondery-share.net/box/u/0/folders/9ZtRe4wQmN2bVx7kLp5sHc8jYd3fGa1oU

```html
<!DOCTYPE html>
<html lang="en">
<head>
<meta charset="utf-8">
<title>The Vorelka Crest Lodge — Kyrgyzstan 2025 Brochure</title>
<link rel="stylesheet" href="https://fonts.googleapis.com/css2?family=Zilla+Slab:wght@700&family=Montserrat:wght@300;400;600;700&display=swap">
<style>
:root{
  --canvas:#000;
  --paper:#ffffff;
  --panel:#e3e3e3;
  --ink:#161616;
  --muted:#4a4a4a;
  --night:#232323;
  --white:#ffffff;
  --slab:"Zilla Slab", Georgia, serif;
  --sans:"Montserrat", Arial, sans-serif;
}
*{margin:0;padding:0;box-sizing:border-box}
html,body{width:960px;height:1200px;overflow:hidden;background:var(--canvas)}
.spread{position:relative;width:960px;height:1200px;background:var(--canvas)}
.page{position:absolute;width:258px;height:333px;overflow:hidden;background:var(--paper);color:var(--ink);font-family:var(--sans)}
.abs{position:absolute}
.photo{position:absolute}
.col-1{left:81px}.col-2{left:351px}.col-3{left:622px}
.row-1{top:87px}.row-2{top:434px}.row-3{top:779px}

.slab{font-family:var(--slab);font-weight:700;line-height:1.1}
.body-copy{font-size:2.6px;line-height:1.55;color:var(--muted)}
.photo-title{color:var(--white);font-size:9.5px;text-shadow:0 1px 2px rgba(0,0,0,.4)}
.section-head{font-size:7px;margin-bottom:4px}
.quote{font-family:var(--slab);font-weight:700;font-size:15px;line-height:1}
.panel{background:var(--panel)}
.brand-word{font-family:var(--sans);font-weight:700;letter-spacing:.02em}

/* cover */
.cover-brand{left:0;width:258px;top:22px;text-align:center;font-size:6px;color:var(--ink)}
.cover-brand .dot{display:inline-block;width:10px;height:10px;border-radius:50%;background:var(--ink);vertical-align:middle;margin-right:3px}
.lodge-line{font-family:var(--sans);font-weight:400;letter-spacing:.28em;text-transform:uppercase}
.cover-year{left:0;width:258px;top:304px;text-align:center;color:var(--white);font-size:9px;font-weight:300;letter-spacing:.3em}

/* pricing */
.price-row{display:flex;justify-content:space-between;font-size:3px;font-weight:600;margin-bottom:8px}
.inc-group{font-size:2.6px;margin-bottom:10px}
.inc-group .label{font-weight:700;text-transform:uppercase;border-bottom:.5px solid #999;border-left:.5px solid #999;padding:0 0 2px 1px;display:inline-block;width:60px;margin-bottom:5px}
.inc-group li{list-style:none;margin-bottom:8px;color:var(--muted)}
.inc-group li::before{content:"";display:inline-block;width:1.6px;height:1.6px;border-radius:50%;background:var(--ink);margin-right:2px;vertical-align:middle}

.collage-title{left:0;width:258px;text-align:center;color:var(--white);font-size:16px;text-shadow:0 1px 3px rgba(0,0,0,.45)}
.caps-copy{font-size:2.9px;font-weight:700;text-transform:uppercase;line-height:1.55;color:var(--white)}

/* back cover */
.back{background:var(--night);color:var(--white)}
.back-contact{left:0;width:258px;top:317px;display:flex;justify-content:center;gap:6px;font-size:2.8px;font-weight:600}
</style>
</head>
<body>
<main class="spread">

  <!-- Cover -->
  <section class="page col-1 row-1 cover">
    <div class="photo" style="inset:0;background:linear-gradient(180deg,#e9ecef 0%,#c9ced3 22%,#a9a094 42%,#9c8366 60%,#7b6a58 78%,#5a534c 100%)" role="img" aria-label="Hunter in camouflage kneeling on a rocky slope glassing a wide mountain valley under cloudy sky"></div>
    <div class="abs cover-brand brand-word"><span class="dot"></span>RIDGEWARD</div>
    <div class="abs lodge-line" style="left:0;width:258px;top:103px;text-align:center;font-size:5px;color:#222">The Vorelka Crest Lodge</div>
    <div class="abs cover-year">KYRGYZSTAN 2025</div>
  </section>

  <!-- Intro -->
  <section class="page col-2 row-1">
    <div class="photo" style="left:0;top:0;width:121px;height:162px;background:linear-gradient(160deg,#cfcfcf,#8b8b8b 55%,#e6e6e6)" role="img" aria-label="Black and white portrait of a hunter seated in snow behind a Marco Polo ram trophy"></div>
    <div class="abs panel" style="left:121px;top:29px;width:137px;height:106px;padding:7px 5px 0 8px">
      <h1 class="slab" style="font-size:9px;margin-bottom:6px">A Hunter's Paradise:<br>Where Luxury Roams Free</h1>
      <p class="body-copy" style="margin-bottom:3px">Renowned as one of the best mountain hunting lodges in the world, this Kyrgyzstan camp offers adventure and luxury in the majestic Tian Shan Mountains. Hunt Marco Polo sheep and Ibex across rugged terrain, then relax in unparalleled comfort.</p>
      <p class="body-copy">Unwind in this secluded oasis, surrounded by breathtaking panoramas of the Kyrgyz landscape. This is where the adventure of the hunt seamlessly blends with the comforts of an unparalleled wilderness retreat.</p>
    </div>
    <div class="photo" style="left:0;top:162px;width:258px;height:171px;background:linear-gradient(180deg,#0d2a9a 0%,#1e47c4 38%,#9a7a5c 58%,#7b8a4c 80%,#4f6a2c 100%)" role="img" aria-label="Wooden lodge building in a green valley below red rock peaks and deep blue sky"></div>
  </section>

  <!-- Hunt details A -->
  <section class="page col-3 row-1">
    <div class="photo" style="left:0;top:0;width:258px;height:172px;background:linear-gradient(180deg,#3c4a63 0%,#c9a28a 30%,#9aa3ad 55%,#6e7078 80%,#4b4a50 100%)" role="img" aria-label="Hunter posing with a large Marco Polo ram on snowy high ground at sunset"></div>
    <h2 class="abs slab photo-title" style="left:25px;top:158px">Hunt Details</h2>
    <div class="abs" style="left:25px;top:186px;width:110px">
      <h3 class="slab section-head">Highlights</h3>
      <p class="body-copy">Experience an unforgettable hunting adventure in Kyrgyzstan's majestic Tian Shan Mountains. Pursue the elusive Marco Polo sheep and Siberian Ibex, hunting on horseback alongside seasoned local guides. Sharpen your long-range shooting skills, as accuracy at 400-500 meters may be required. The breathtaking scenery, from towering peaks to vast valleys, provides a stunning backdrop. This unique combination of challenging hunts and unparalleled landscapes creates a truly once-in-a-lifetime experience.</p>
    </div>
    <div class="abs panel" style="left:0;top:280px;width:154px;height:35px"></div>
    <div class="abs" style="left:25px;top:260px;width:118px">
      <h3 class="slab section-head" style="font-size:6.5px">Getting There<br>Recommended Route</h3>
      <p class="body-copy">International flights typically arrive at Manas International Airport (FRU) in Bishkek, Kyrgyzstan, often with layovers in Istanbul or Dubai. Upon arrival, our team will assist with firearms clearance. For guests arriving late, overnight accommodations in Bishkek can be arranged. From Bishkek, hunters have two options to reach the hunting area in the mountains: a 12-hour scenic drive or a 2.5-hour helicopter flight.</p>
    </div>
    <div class="abs quote" style="left:154px;top:176px">“</div>
    <div class="abs" style="left:164px;top:186px;width:75px">
      <h3 class="slab section-head">Property Facts</h3>
      <p class="body-copy">Nestled deep within the majestic Tian Shan mountains, this hunting camp, a unique endeavor by the Kyrgyz government, offers an unparalleled wilderness experience. While the eight luxurious rooms each provide private bathrooms and unexpected amenities like reliable Wi-Fi – a true rarity in such a remote setting – it is the communal spaces that truly capture the grandeur of the surroundings. The lounge area, with its striking floor-to-ceiling windows, frames breathtaking panoramic views of the rugged landscape. This blend of modern comforts and unspoiled wilderness creates a hunting retreat unlike any other.</p>
    </div>
    <div class="abs quote" style="left:237px;top:286px">”</div>
  </section>

  <!-- Hunt details B -->
  <section class="page col-1 row-2">
    <div class="photo" style="left:0;top:0;width:258px;height:142px;background:linear-gradient(180deg,#2f67b8 0%,#9cbde0 30%,#a06c4c 52%,#8c8a80 72%,#5c6a3c 100%)" role="img" aria-label="Braided river valley with red cliffs and sunburst through clouds"></div>
    <h2 class="abs slab photo-title" style="left:26px;top:129px">Hunt Details</h2>
    <div class="abs" style="left:26px;top:166px;width:102px">
      <h3 class="slab section-head">Highlights</h3>
      <p class="body-copy">Experience an unforgettable hunting adventure in Kyrgyzstan's majestic Tian Shan Mountains. Pursue the elusive Marco Polo sheep and Siberian Ibex, hunting on horseback alongside seasoned local guides. Sharpen your long-range shooting skills, as accuracy at 400-500 meters may be required. The breathtaking scenery, from towering peaks to vast valleys, provides a stunning backdrop. This unique combination of challenging hunts and unparalleled landscapes creates a truly once-in-a-lifetime experience.</p>
    </div>
    <div class="abs quote" style="left:127px;top:156px">“</div>
    <div class="abs" style="left:138px;top:166px;width:100px">
      <h3 class="slab section-head">Property Facts</h3>
      <p class="body-copy">Nestled deep within the majestic Tian Shan mountains, this hunting camp, a unique endeavor by the Kyrgyz government, offers an unparalleled wilderness experience. While the eight luxurious rooms each provide private bathrooms and unexpected amenities like reliable Wi-Fi – a true rarity in such a remote setting – it is the communal spaces that truly capture the grandeur of the surroundings. The lounge area, with its striking floor-to-ceiling windows, frames breathtaking panoramic views of the rugged landscape. This blend of modern comforts and unspoiled wilderness creates a hunting retreat unlike any other.</p>
    </div>
    <div class="abs quote" style="left:233px;top:245px">”</div>
    <div class="abs panel" style="left:0;top:262px;width:258px;height:49px;padding:3px 26px 0">
      <h3 class="slab section-head" style="font-size:6.5px;margin-bottom:3px">Getting There<br>Recommended Route</h3>
      <p class="body-copy">International flights typically arrive at Manas International Airport (FRU) in Bishkek, Kyrgyzstan, often with layovers in Istanbul or Dubai. Upon arrival, our team will assist with firearms clearance. For guests arriving late, overnight accommodations in Bishkek can be arranged. From Bishkek, hunters have two options to reach the hunting area in the mountains: a 12-hour scenic drive or a 2.5-hour helicopter flight.</p>
    </div>
  </section>

  <!-- Dates & pricing -->
  <section class="page col-2 row-2">
    <div class="abs panel" style="left:0;top:0;width:94px;height:333px"></div>
    <div class="abs" style="left:12px;top:26px;width:80px">
      <h2 class="slab" style="font-size:9px;margin-bottom:8px">Dates &amp; Pricing</h2>
      <h3 class="slab" style="font-size:6.5px;margin-bottom:5px">Season Dates</h3>
      <div style="display:flex;align-items:center;gap:4px">
        <div class="slab" style="font-size:6px">August<br><span style="font-size:4.5px">15th 2025</span></div>
        <svg width="6" height="6" viewBox="0 0 6 6"><path d="M1.5 1 L4 3 L1.5 5" fill="none" stroke="#161616" stroke-width=".8"/></svg>
        <div class="slab" style="font-size:6px">November<br><span style="font-size:4.5px">30th 2025</span></div>
      </div>
    </div>
    <div class="photo" style="left:0;top:78px;width:94px;height:140px;background:linear-gradient(180deg,#d9dadb 0%,#b7aa96 35%,#8a7a66 65%,#6a5c4c 100%)" role="img" aria-label="Hunter kneeling behind a Siberian ibex on a rocky mountainside"></div>
    <div class="photo" style="left:94px;top:0;width:164px;height:109px;background:linear-gradient(135deg,#c98a3c 0%,#d9a05a 45%,#a86a2c 100%)" role="img" aria-label="Timber-walled lounge with white sofas and mounted trophies"></div>
    <div class="abs" style="left:12px;top:227px;width:76px">
      <h3 class="slab" style="font-size:9px;margin-bottom:6px">Pricing</h3>
      <div class="price-row"><span>MARCO POLO AND<br>IBEX COMBO</span><span>$39,500<br>(min. 2 hunters)</span></div>
      <div class="price-row"><span>MARCO POLO<br>ARGALI -</span><span>$32,500<br>(min. 2 hunters)</span></div>
      <div class="price-row"><span>MID ASIAN<br>IBEX -</span><span>$10,500<br>(min. 2 hunters)</span></div>
      <div style="font-size:3px;font-weight:600;text-align:center;margin-bottom:5px">POPULAR ADD ONS</div>
      <div class="price-row"><span style="font-weight:400">WOLF<br>(Opportunistic)</span><span>$2,500</span></div>
      <div class="price-row"><span style="font-weight:400">Extra Ibex</span><span>$5,500</span></div>
    </div>
    <div class="abs" style="left:124px;top:148px;width:125px">
      <h3 class="slab" style="font-size:7px;margin-bottom:4px">Inclusions</h3>
      <ul class="inc-group"><span class="label">Guided Hunt -</span>
        <li>5-day guided horseback hunt for Marco Polo Argali, Ibex or both</li>
        <li>Exclusive access to some of the finest hunting areas in Kyrgyzstan</li>
        <li>Trophy skinning and field preparation</li>
      </ul>
      <ul class="inc-group"><span class="label">Food &amp; Drink -</span>
        <li>Chef-prepared breakfast, packed lunch and dinner</li>
        <li>A selection of non alcoholic beverages</li>
      </ul>
      <ul class="inc-group"><span class="label">Travel &amp; Logistics</span>
        <li>Pre-arrival custom planning with the Ridgeward team</li>
        <li>Round trip, fixed-time airport transfers to Bishkek</li>
      </ul>
    </div>
  </section>

  <!-- Adventures -->
  <section class="page col-3 row-2">
    <div class="photo" style="left:0;top:0;width:123px;height:185px;background:linear-gradient(180deg,#bfc1c4 0%,#9a9a98 45%,#6c665c 100%)" role="img" aria-label="Group of hunters and guides with horses on a rocky ridge"></div>
    <p class="abs caps-copy" style="left:12px;top:11px;width:85px">A horseback ride you'll never forget. Challenging hunts for prized game. A stunning camp to revitalize your spirit. This is the hunt of a lifetime.</p>
    <div class="photo" style="left:123px;top:0;width:135px;height:185px;background:linear-gradient(160deg,#9cc3de 0%,#5e88a8 50%,#2f4a5e 100%)" role="img" aria-label="Close view of curled ram horns resting on blue-tinted snow"></div>
    <div class="photo" style="left:0;top:185px;width:138px;height:148px;background:linear-gradient(180deg,#6f8494 0%,#5b6670 50%,#3a3f44 100%)" role="img" aria-label="Hunter lying prone behind a scoped rifle on rocks"></div>
    <div class="photo" style="left:138px;top:185px;width:120px;height:148px;background:linear-gradient(180deg,#8a7a6a 0%,#a5937e 50%,#6b5a48 100%)" role="img" aria-label="Rider on a white horse climbing a scree slope"></div>
    <h2 class="abs slab collage-title" style="top:170px">The Adventures</h2>
  </section>

  <!-- Lodge -->
  <section class="page col-1 row-3">
    <div class="photo" style="left:0;top:0;width:125px;height:178px;background:linear-gradient(135deg,#c88438 0%,#dba462 50%,#9a5e26 100%)" role="img" aria-label="Lodge lounge with white sofas, wooden walls and trophy mounts"></div>
    <div class="photo" style="left:125px;top:0;width:133px;height:88px;background:linear-gradient(180deg,#0c2a8c 0%,#2350b8 60%,#8a6a3c 80%,#6c5a36 100%)" role="img" aria-label="Exterior of the wooden lodge under a deep blue sky"></div>
    <p class="abs caps-copy" style="left:130px;top:12px;width:88px;font-size:2.7px">Beyond the reach of ordinary travel lies a hidden world of spectacular beauty and unrivaled hunting. Our Kyrgyzstan experience is crafted for the discerning sportsman, offering access to pristine wilderness and luxurious accommodations. This is hunting elevated to an art form.</p>
    <div class="photo" style="left:125px;top:88px;width:133px;height:90px;background:linear-gradient(135deg,#b87434 0%,#d49a58 50%,#8c5622 100%)" role="img" aria-label="Games room with billiard table and high timber ceiling"></div>
    <div class="photo" style="left:0;top:178px;width:104px;height:155px;background:linear-gradient(180deg,#6a3c16 0%,#c27a34 50%,#8a6a54 100%)" role="img" aria-label="Long wooden corridor lined with guest room doors"></div>
    <div class="photo" style="left:104px;top:178px;width:154px;height:155px;background:linear-gradient(180deg,#8a4e1c 0%,#c88238 50%,#1fb3a8 85%,#3a2a1a 100%)" role="img" aria-label="Billiard table with turquoise cloth beneath chandeliers"></div>
    <h2 class="abs slab collage-title" style="top:162px">The Lodge</h2>
  </section>

  <!-- Back cover -->
  <section class="page col-2 row-3 back">
    <div class="abs brand-word" style="left:0;width:258px;top:180px;text-align:center;font-size:8px"><span style="display:inline-block;width:12px;height:12px;border-radius:50%;background:var(--white);vertical-align:middle;margin-right:4px"></span>RIDGEWARD</div>
    <div class="abs lodge-line" style="left:0;width:258px;top:301px;text-align:center;font-size:3.2px">The Vorelka Crest Lodge</div>
    <div class="abs back-contact">
      <span>www.ridgeward-hunts.com</span><span>|</span><span>bookings@ridgeward-hunts.com</span><span>|</span><span>+000 555 0142</span>
    </div>
  </section>

</main>
</body>
</html>
```